International Clinical Software Company needs a new business card design

We are looking for a new business card design for our company that has recently expanded into the UK market, making us a multinational company.
After having rebranded our website and produced a new style guide, we are looking for a business card that is creative and attention grabbing, while being consistent with the style and colour scheme used on the new website, www.plumvora.example
We produce care management technology for the aged care market, but the main aspect we aim to communicate is the human element of our software, and the way it assists in providing better care for aged people, and stronger relationships between aged people and the staff that care for them.
Our current business card is a dark green with gold text, which makes the text quite difficult to read, not very aesthetically appealing and the colour scheme looks quite dated.
We would like something fresh and modern, that can still be colourful but doesn't use large blocks of dark colour, and uses the colours within our logo.
Something tying in with the leaves that are used in our logo could work quite nicely, along with the Autumn/Fall colours of soft greens, yellows and reds (also in our existing logo). However also happy to look at fresh, completely out of the box ideas we may not have yet considered.
Target Market(s)
The people that receive this business card work in the aged card or health industry and are either corporate/management level staff or clinical (Registered Nurses, care workers etc.)
Industry/Entity Type
Health Product
Contact Information for Business Card
Company Name - BrindlewayCare
Company locations: United Kingdom, Australia, New Zealand
Staff Details:
Staff name: Derek Mallow
Staff job title: Executive Chairman
Staff email: d.mallow@plumvora.example
Office phone number: 01742 918576
Font styles to use
Other font styles liked:
- Calibri
Requirements
Must have
- Must include the BrindlewayCare brand name in it's current font
- Must include logo (3 leaves in gold circle)
- Must include Business Card Details
Nice to have
- Elements of gold
- White space
- Something autumn themed but not too cliched
Should not have
- No blue - used by a major competitor and we would like to differentiate from them
- Large blocks of dark green colour (the green that appears in our leaves on the logo on our current business card is the background colour and it is far too dark)

```html
<!DOCTYPE html>
<html lang="en">
<head>
<meta charset="utf-8">
<title>BrindlewayCare business card</title>
<link rel="stylesheet" href="https://fonts.googleapis.com/css2?family=Open+Sans:wght@300;400;700&display=swap">
<style>
  :root {
    --backdrop: #8d8d8b;
    --card-white: #ffffff;
    --gold: #b39b6b;
    --gold-line: #a88f5d;
    --leaf-green: #5f8a2c;
    --leaf-red: #c23f52;
    --text-light: #ffffff;
    --autumn-orange: #e8832a;
    --autumn-yellow: #f3c93c;
    --autumn-pale: #e4ecb4;
    --autumn-red: #d8522a;
  }
  * { margin: 0; padding: 0; box-sizing: border-box; }
  html, body {
    width: 1200px; height: 900px; overflow: hidden;
    background: var(--backdrop);
    font-family: "Open Sans", Calibri, Arial, sans-serif;
  }
  .canvas { position: relative; width: 1200px; height: 900px; }
  .card {
    position: absolute; width: 680px; height: 389px; overflow: hidden;
    box-shadow: 0 6px 18px rgba(0,0,0,.25);
  }

  /* Back of card: autumn photograph */
  .card-back { left: 420px; top: 40px; }
  .autumn-photo {
    position: absolute; inset: 0;
    background:
      radial-gradient(circle at 18% 30%, var(--autumn-yellow) 0, transparent 38%),
      radial-gradient(circle at 45% 12%, var(--autumn-red) 0, transparent 22%),
      radial-gradient(circle at 92% 55%, var(--autumn-orange) 0, transparent 25%),
      radial-gradient(circle at 70% 40%, var(--autumn-pale) 0, transparent 40%),
      linear-gradient(120deg, var(--autumn-orange) 0%, var(--autumn-yellow) 45%, var(--autumn-pale) 75%, var(--autumn-yellow) 100%);
  }
  .back-brand {
    position: absolute; right: 48px; top: 150px;
    display: flex; flex-direction: column; align-items: center; gap: 10px;
  }
  .brand-circle {
    width: 92px; height: 92px; border-radius: 50%;
    border: 3px solid var(--gold-line);
  }
  .back-brand .brand-name {
    font-weight: 400; font-size: 20px; color: var(--gold-line); letter-spacing: .5px;
  }

  /* Front of card: brand and contact details */
  .card-front { left: 120px; top: 471px; background: var(--card-white); }
  .card-front svg.sweep { position: absolute; inset: 0; }
  .front-brand {
    position: absolute; left: 40px; top: 84px; width: 290px;
    display: flex; flex-direction: column; align-items: center; gap: 16px;
  }
  .front-brand .brand-circle { width: 86px; height: 86px; }
  .front-brand .brand-name {
    font-weight: 300; font-size: 37px; color: var(--gold); letter-spacing: .5px;
  }
  .contact {
    position: absolute; right: 48px; top: 120px; text-align: right;
    color: var(--text-light); line-height: 1.3;
  }
  .contact .person-name { font-weight: 700; font-size: 22px; }
  .contact .person-title { font-size: 16px; font-weight: 400; }
  .contact .email { font-size: 15px; margin-top: 10px; display: flex; align-items: center; justify-content: flex-end; gap: 8px; }
  .contact .email svg { width: 14px; height: 14px; }
  .contact .locations { font-size: 16px; margin-top: 14px; }
</style>
</head>
<body>
<main class="canvas">

  <section class="card card-back">
    <div class="autumn-photo" role="img" aria-label="Photograph of golden and red autumn maple leaves against a soft blurred background"></div>
    <div class="back-brand">
      <div class="brand-circle"></div>
      <span class="brand-name">BrindlewayCare</span>
    </div>
  </section>

  <section class="card card-front">
    <svg class="sweep" viewBox="0 0 680 389" width="680" height="389" aria-hidden="true">
      <path d="M322,0 L341,0 C410,110 406,230 356,310 C386,230 392,120 322,0 Z" fill="var(--leaf-green)"/>
      <path d="M392,190 C380,300 310,360 206,389 L228,389 C330,350 388,290 392,190 Z" fill="var(--leaf-red)"/>
      <path d="M346,0 C426,120 410,300 236,389 L680,389 L680,0 Z" fill="var(--gold)"/>
    </svg>

    <div class="front-brand">
      <div class="brand-circle"></div>
      <span class="brand-name">BrindlewayCare</span>
    </div>

    <div class="contact">
      <div class="person-name">Derek Mallow</div>
      <div class="person-title">Executive Chairman</div>
      <div class="email">d.mallow@plumvora.example
        <svg viewBox="0 0 24 24" aria-hidden="true"><path fill="#fff" d="M6.6 10.8a15.1 15.1 0 0 0 6.6 6.6l2.2-2.2a1 1 0 0 1 1-.25 11.4 11.4 0 0 0 3.6.57 1 1 0 0 1 1 1V20a1 1 0 0 1-1 1A17 17 0 0 1 3 4a1 1 0 0 1 1-1h3.5a1 1 0 0 1 1 1c0 1.25.2 2.45.57 3.57a1 1 0 0 1-.25 1z"/></svg>
      </div>
      <div class="locations">United Kingdom, Australia<br>New Zealand</div>
    </div>
  </section>

</main>
</body>
</html>
```